Website for a Pittsburgh Musical Production

We are creating a website for a musical stage production. Content and copy is included below. We are targeting production in early 2023.

```html
<!DOCTYPE html>
<html lang="en">
<head>
<meta charset="utf-8">
<title>Monstrum – The Rock Opera</title>
<link href="https://fonts.googleapis.com/css2?family=PT+Sans:wght@400;700&family=Arimo:wght@400&display=swap" rel="stylesheet">
<style>
:root{
  --green:#5b7d4c;
  --green-text:#5e7f4e;
  --hero-bg:#1d221d;
  --about-bg:#161817;
  --gallery-bg:#0e100f;
  --promo-bg:#121413;
  --footer-bg:#0b0c0b;
  --white:#ffffff;
  --muted:#8b8d8b;
  --body-light:#e6e6e6;
}
*{margin:0;padding:0;box-sizing:border-box}
html,body{width:1200px;height:3052px;overflow:hidden;background:var(--footer-bg)}
body{position:relative;font-family:"PT Sans",sans-serif;color:var(--white)}
.block{position:absolute;left:0;width:1200px}
.abs{position:absolute}
.btn{position:absolute;display:flex;align-items:center;justify-content:center;background:var(--green);color:var(--white);font-family:"PT Sans",sans-serif;font-weight:700;border-radius:3px;text-decoration:none}
.nav-list{list-style:none;display:flex;justify-content:center;gap:66px;font-weight:700;font-size:15px;text-transform:uppercase;width:1200px}
.nav-list li{white-space:nowrap}

/* hero */
.hero{top:0;height:721px;background:radial-gradient(ellipse at 70% 40%,#283028 0%,var(--hero-bg) 60%,#151915 100%)}
.hero-art{left:112px;top:24px;width:322px;height:664px;background:radial-gradient(ellipse at 50% 45%,#6f9458 0%,#4a6a3c 45%,rgba(29,34,29,0) 75%)}
.brand{left:520px;top:200px;width:500px;text-align:center;color:var(--green-text);font-weight:700;line-height:1}
.brand-name{font-size:96px;letter-spacing:-1px}
.brand-sub{font-size:30px;margin-top:4px;padding-left:170px}
.hero-text{left:500px;top:395px;width:540px;text-align:center;font-size:18px;line-height:31px}
.hero .btn{left:686px;top:518px;width:167px;height:57px;font-size:20px}

/* nav */
.main-nav{top:721px;height:71px;background:var(--green);display:flex;align-items:center}

/* about */
.about{top:792px;height:618px;background:var(--about-bg)}
.about-art{left:140px;top:99px;width:452px;height:452px;border-radius:50%;background:radial-gradient(circle at 50% 45%,#3a3d3b 0%,#242725 55%,#1e201f 100%)}
.section-title{font-weight:700;font-size:48px;color:var(--green-text);line-height:1;text-transform:uppercase}
.about .section-title{left:667px;top:97px}
.rule{position:absolute;height:3px;background:var(--white)}
.about .rule{left:667px;top:161px;width:57px}
.about-text{left:669px;top:189px;width:398px;font-family:"Arimo",sans-serif;font-size:13.3px;line-height:25.7px;color:var(--muted);text-align:justify;word-break:break-all}
.about .btn{left:675px;top:466px;width:148px;height:56px;font-size:17px}

/* gallery */
.gallery{top:1410px;height:770px;background:var(--gallery-bg)}
.gallery .section-title{left:0;width:1200px;text-align:center;top:58px}
.gallery .rule{left:571px;top:117px;width:57px}
.gallery-grid{position:absolute;left:111px;top:158px;display:grid;grid-template-columns:repeat(3,311px);grid-auto-rows:265px;column-gap:22px;row-gap:23px}
.photo{display:block}
.photo-1{background:linear-gradient(160deg,#2a2e7a,#1b1d4a 60%,#6b4a3a)}
.photo-2{background:linear-gradient(170deg,#2a0f6e,#8a2bd0 40%,#3a1260 70%,#170b30)}
.photo-3{background:linear-gradient(180deg,#241a3a,#3a2a50 55%,#120e1c)}
.photo-4{background:linear-gradient(90deg,#8a0c10,#1a0a14 40%,#14101a 60%,#8a0c10)}
.photo-5{background:radial-gradient(circle at 50% 55%,#6a5040,#2a2220 60%,#121010)}
.photo-6{background:linear-gradient(160deg,#1a1a2a,#3a3aa0 55%,#b08ad0 70%,#141428)}

/* promo */
.promo{top:2180px;height:495px;background:linear-gradient(90deg,#101211 0%,var(--promo-bg) 50%,#1c1e1d 100%)}
.promo-art{left:690px;top:0;width:510px;height:495px;background:radial-gradient(ellipse at 55% 60%,#4a4c4b 0%,#2a2c2b 45%,rgba(18,20,19,0) 75%)}
.promo-title{left:110px;top:112px;font-size:36px;font-weight:700;line-height:1;text-transform:uppercase}
.promo-text{left:113px;top:177px;width:520px;font-family:"Arimo",sans-serif;font-size:13.3px;line-height:28.4px;color:var(--body-light)}
.promo .btn{left:113px;top:341px;width:155px;height:57px;font-size:17px}

/* footer */
.footer{top:2675px;height:377px;background:var(--footer-bg)}
.footer .brand{left:450px;top:34px;width:300px}
.footer .brand-name{font-size:64px}
.footer .brand-sub{font-size:22px;padding-left:120px}
.footer-nav{left:0;top:179px}
.social{left:496px;top:242px}
.copyright{left:0;top:312px;width:1200px;text-align:center;font-family:"Arimo",sans-serif;font-size:15px;color:#d8d8d8}
</style>
</head>
<body>

<header class="block hero">
  <div class="abs hero-art" role="img" aria-label="Green sketched illustration of the creature's portrait"></div>
  <div class="abs brand">
    <div class="brand-name">Monstrum</div>
    <div class="brand-sub">the rock opera</div>
  </div>
  <p class="abs hero-text">Sed ut perspiciatis unde omnis iste natus error sit voluptatem accusantium doloremque laudantium, totam rem aperiam, eaque architecto beatae vitae dicta sunt explicabo.</p>
  <a class="btn" href="#">Read More</a>
</header>

<nav class="block main-nav">
  <ul class="nav-list">
    <li>Home</li><li>About Us</li><li>Services</li><li>Gallery</li><li>Features</li><li>News</li><li>Contact Us</li>
  </ul>
</nav>

<section class="block about">
  <div class="abs about-art" role="img" aria-label="Sketched illustration of a singer with a microphone inside a dark circle"></div>
  <h2 class="abs section-title">About Us</h2>
  <span class="rule"></span>
  <p class="abs about-text">Sed ut perspiciatis unde omnis iste natus error sit voluptatem accusantium doloremque laudantium, totam rem aperiam, eaque ipsa quae ab illo inventore veritatis et quasi architecto beatae vitae dicta sunt explicabo. Nemo enim ipsam voluptatem quia voluptas sit aspernatur aut odit aut fugit, sed quia consequuntur magni dolores eos qui ratione voluptatem sequi nesciunt. Neque porro quisquam est, qui dolorem ipsum quia dolor sit amet, consectetur, adipi velit, sed quia non numquam eius modi tempora incidunt ut magnam aliquam quaerat voluptatem. Ut enim ad minima veniam, quis nostrum exercitationem ullam corporis suscipit</p>
  <a class="btn" href="#">READ MORE</a>
</section>

<section class="block gallery">
  <h2 class="abs section-title">Photo Gallery</h2>
  <span class="rule"></span>
  <div class="gallery-grid">
    <div class="photo photo-1" role="img" aria-label="Drummers performing on a blue-lit stage"></div>
    <div class="photo photo-2" role="img" aria-label="Purple stage lights over empty theatre seats"></div>
    <div class="photo photo-3" role="img" aria-label="Audience silhouettes in front of a lit stage"></div>
    <div class="photo photo-4" role="img" aria-label="Two performers between red stage curtains"></div>
    <div class="photo photo-5" role="img" aria-label="Performer addressing the audience under a spotlight"></div>
    <div class="photo photo-6" role="img" aria-label="Wide view of a concert hall and lit stage"></div>
  </div>
</section>

<section class="block promo">
  <div class="abs promo-art" role="img" aria-label="Grey theatre masks of comedy and tragedy"></div>
  <h2 class="abs promo-title">Sed ut perspiciatis unde omnis</h2>
  <p class="abs promo-text">Nemo enim ipsam voluptatem quia voluptas sit aspernatur aut odit aut fugit, sed quia consequuntur magni dolores eos qui ratione voluptatem sequi nesciunt. Neque porro quisquam est, qui dolo rem ipsum quia dolor sit amet, consectetur, adipisci velit, sed quia non numquam eius modi tempora incidunt ut labore et dolore magnam aliquam voluptas sit aspernatur&nbsp; quaerat voluptatem.</p>
  <a class="btn" href="#">READ MORE</a>
</section>

<footer class="block footer">
  <div class="abs brand">
    <div class="brand-name">Monstrum</div>
    <div class="brand-sub">the rock opera</div>
  </div>
  <ul class="abs nav-list footer-nav">
    <li>Home</li><li>About Us</li><li>Services</li><li>Gallery</li><li>Features</li><li>News</li><li>Contact Us</li>
  </ul>
  <svg class="abs social" width="208" height="40" viewBox="0 0 208 40" role="img" aria-label="Social media links">
    <g fill="none" stroke="#ffffff" stroke-width="1.5">
      <circle cx="18" cy="20" r="17"/>
      <circle cx="61" cy="20" r="17"/>
      <circle cx="104" cy="20" r="17"/>
      <circle cx="147" cy="20" r="17"/>
      <circle cx="190" cy="20" r="17"/>
    </g>
  </svg>
  <p class="abs copyright">© Copyrights 2021 - Monstrum The Rock opera.All Rights Reserved.</p>
</footer>

</body>
</html>
```